Book cover for book about Climate Change

Looking for a clean, bold, and attractive cover for a mass-market paperback (5.5"x 8.5") about solving the climate change problem. Title is either "Where the Rivers Meet” or A Harbor Made of Glass” (your choice), subtitle is "A practical field guide to mending the weather — so that the young ones after us inherit steady seasons and open skies," author is Lorne Whitcombe. Thinking that it *might* feature an image of Earth (or a portion thereof) and its very thin layer of atmosphere -- but STRONGLY encourage other ideas too!

Requirements
Nice to have
• Keep it positive — NOT scary doom-and-gloom

```html
<!DOCTYPE html>
<html lang="en">
<head>
<meta charset="utf-8">
<title>Where the Rivers Meet — Book Cover</title>
<link rel="stylesheet" href="https://fonts.googleapis.com/css2?family=Jost:wght@300&family=Tinos&display=swap">
<style>
  :root {
    --backdrop: #f0d6b2;
    --space-top: #140a10;
    --space-mid: #3d1428;
    --space-low: #6e1d44;
    --space-deep: #4a1330;
    --ink: #ffffff;
    --accent: #e8237a;
    --earth-light: #8fb6e6;
    --earth-mid: #2f5f9e;
    --earth-dark: #0f2346;
  }
  * { margin: 0; padding: 0; box-sizing: border-box; }
  html, body {
    width: 1200px;
    height: 1200px;
    overflow: hidden;
    background: var(--backdrop);
  }
  .cover {
    position: absolute;
    left: 240px;
    top: 44px;
    width: 720px;
    height: 1112px;
    overflow: hidden;
    color: var(--ink);
  }
  .starfield {
    position: absolute;
    inset: 0;
    background:
      radial-gradient(ellipse 80% 45% at 60% 75%, rgba(150, 40, 90, 0.55), transparent 70%),
      linear-gradient(180deg, var(--space-top) 0%, var(--space-mid) 35%, var(--space-low) 70%, var(--space-deep) 100%);
  }
  .subtitle {
    position: absolute;
    top: 96px;
    left: 50px;
    right: 50px;
    font-family: "Tinos", "Times New Roman", serif;
    font-size: 20.5px;
    line-height: 31px;
    text-transform: uppercase;
    text-align: center;
    letter-spacing: 0.2px;
  }
  .subtitle .highlight { color: var(--accent); }
  .title {
    position: absolute;
    top: 218px;
    left: 0;
    right: 0;
    font-family: "Jost", "Futura", sans-serif;
    font-weight: 300;
    font-size: 168px;
    line-height: 132px;
    text-align: center;
    text-transform: uppercase;
    letter-spacing: -2px;
  }
  .title-line { display: block; white-space: nowrap; }
  .title-line--last { display: flex; justify-content: center; align-items: center; gap: 14px; }
  .globe {
    display: inline-block;
    width: 118px;
    height: 118px;
    border-radius: 50%;
    background: radial-gradient(circle at 38% 35%, var(--earth-light) 0%, var(--earth-mid) 45%, var(--earth-dark) 100%);
    box-shadow: 0 0 22px rgba(170, 200, 255, 0.55);
  }
  .flare {
    position: absolute;
    top: 753px;
    left: 180px;
    width: 400px;
    height: 3px;
    background: linear-gradient(90deg, transparent, rgba(200, 220, 255, 0.9) 50%, transparent);
  }
  .author {
    position: absolute;
    top: 994px;
    left: 0;
    right: 0;
    font-family: "Tinos", "Times New Roman", serif;
    font-size: 46px;
    letter-spacing: 8px;
    text-align: center;
    text-transform: uppercase;
  }
</style>
</head>
<body>
  <main class="cover">
    <div class="starfield" role="img" aria-label="Starry night sky fading from black into deep magenta"></div>
    <p class="subtitle">A <span class="highlight">practical</span> field guide to <span class="highlight">mending</span> the weather — so that the young ones after us inherit steady seasons and open skies</p>
    <h1 class="title">
      <span class="title-line">Where</span>
      <span class="title-line">the</span>
      <span class="title-line">Rivers</span>
      <span class="title-line title-line--last">Meet<span class="globe" role="img" aria-label="Planet Earth seen from space, lit at the edge"></span></span>
    </h1>
    <div class="flare"></div>
    <p class="author">Lorne Whitcombe</p>
  </main>
</body>
</html>
```